RIVERSTONE PULSE GYM FLYER DESIGN

We want a flyer designed for our gym. We have an example of a flyer which we like and I have put it into the images I have uploaded. I would like to recreate using our pictures, so its a pretty straight forward job. We also want to put our weekly timetable on the back of the flyer. We would like the size of the flyer to be A5.

Target Market(s)

FITNESS

Industry/Entity Type

Gym

Colors
33a6d7
ffffff

Requirements
Must have
• We just want to recreate the flyer but we must have the following info on the flyer and we want our timetable on the back of the flyer which you can get from this link: http://www.riverstonepulsegym-example.com/timetable
• Riverstone Pulse Gym is a fun community of humble people. Our goal is to help guide you towards a fitter, healthier lifestyle!
• Our Programs
• HIIT
• High intensity interval training is 30-45 minutes of fat burning fun. The class is a mix of cardio, bodyweight and some resistance movements.
• Conditioning
• A full hour of strength, cardio and bodyweight training to get you in tip top shape. Expect a mix of barbells, kettlebells, rowing machines, bikes and other training methods.
• BWS
• This is our big Friday session to set you up for the weekend. 90 minutes of hard training that is done with a team emphasis. From heavy lifting to cardio triathlons, this class has it all but not for the faint hearted.
• Muay Thai
• Commonly known as the science of 8 limbs you will learn how to punch, kick, knee and elbow. Thailands national sport is a great way to get your fitness kick. We train the complete beginner all the way to international fighters so you are in great hands.
• Kids Muay Thai
• Our junior program starts from age 6 onwards. Muay Thai is a great way for kids to get active and fit while learning new skills. Training in martial arts also teaches self discipline and socialisation skills.
• Yoga
• A combination of physical and mental practises that will leave you focused and refreshed for whatever the week throws at you. We always recommend our yoga classes as a great way to balance the high intensity training we offer.
• Q-Press
• Strength training with a little bit of conditioning. We regularly update the program and re test lifts to ensure you are making progress and getting stronger.
• CONTACT US
• OUR LOCATION:
• Unit 27C
• 214 Kelvane Road
• Marrow Heath
• Glasgow
• G72QT
• Phone: 07930625184
• Email: info@riverstonepulsegym-example.com
• Web: www.riverstonepulsegym-example.com
Nice to have
• Can use all the picture but if not be good to use the boxing one and the group training one.

```html
<!DOCTYPE html>
<html lang="en">
<head>
<meta charset="utf-8">
<title>Riverstone Pulse Gym Flyer</title>
<link href="https://fonts.googleapis.com/css2?family=Montserrat:wght@400;600;700;800;900&family=Open+Sans:wght@400;600&display=swap" rel="stylesheet">
<style>
  :root {
    --sky: #33a6d7;
    --bright: #1fa4ea;
    --panel: #2aa9e8;
    --deep: #0f8ccf;
    --deeper: #0a7fbf;
    --navy: #0b2f55;
    --ink: #123a5c;
    --white: #ffffff;
  }
  * { margin: 0; padding: 0; box-sizing: border-box; }
  html, body { width: 851px; height: 1200px; overflow: hidden; background: var(--white); }
  .flyer {
    position: relative; width: 851px; height: 1200px; overflow: hidden;
    background: var(--bright);
    font-family: "Montserrat", sans-serif; color: var(--white);
  }
  .backdrop { position: absolute; inset: 0; }
  .photo { position: absolute; }
  .photo-group { left: 290px; top: 0; width: 561px; height: 332px;
    background: linear-gradient(135deg, #3b3f45 0%, #23262b 55%, #4b4038 100%);
    clip-path: polygon(0 0, 100% 0, 100% 74%, 0 100%); }
  .photo-boxing { left: 0; top: 340px; width: 290px; height: 260px;
    background: linear-gradient(120deg, #6d5a4e 0%, #9c7b68 45%, #b3463f 100%); }
  .photo-kettlebell { left: 452px; top: 707px; width: 399px; height: 238px;
    background: linear-gradient(130deg, #2b2e31 0%, #4a4d50 50%, #3a5a33 100%); }

  .brand-name { position: absolute; left: 20px; top: 14px; font-weight: 800; font-size: 21px; line-height: 27px; letter-spacing: 0.3px; }
  .brand-dot { position: absolute; left: 190px; top: 38px; width: 30px; height: 30px; border-radius: 50%; background: var(--white); }
  .intro { position: absolute; left: 30px; top: 150px; width: 250px; font-family: "Open Sans", sans-serif; font-size: 12px; line-height: 15px; }
  .intro p + p { margin-top: 14px; }
  .contact { position: absolute; top: 280px; font-size: 8.5px; font-weight: 700; line-height: 12.4px; }
  .contact.loc { left: 33px; }
  .contact.tel { left: 132px; }
  .contact .web { margin-top: 12px; display: block; font-size: 8.3px; }

  .programs-title { position: absolute; left: 358px; top: 360px; font-weight: 900; font-size: 22px; letter-spacing: -0.5px; }
  .timeline { position: absolute; width: 2px; background: var(--white); }
  .node { position: absolute; width: 24px; height: 24px; border-radius: 50%; background: var(--white); }
  .node::after { content: ""; position: absolute; left: 8px; top: 8px; width: 8px; height: 8px; border-radius: 50%; background: var(--bright); }
  .program { position: absolute; width: 215px; }
  .program h3 { font-weight: 800; font-size: 15px; line-height: 16px; }
  .program p { font-family: "Open Sans", sans-serif; font-size: 7.2px; line-height: 9px; color: var(--ink); }

  .timetable-title { position: absolute; left: 58px; top: 636px; font-weight: 800; font-size: 31px; letter-spacing: 0.5px; }
  .timetable-brand { position: absolute; left: 640px; top: 640px; display: flex; align-items: center; gap: 10px; }
  .timetable-brand .dot { width: 22px; height: 22px; border-radius: 50%; background: var(--white); }
  .timetable-brand span { font-weight: 800; font-size: 13px; line-height: 15px; }

  .day { position: absolute; text-align: right; }
  .day h4 { font-weight: 900; font-size: 25px; line-height: 30px; color: var(--navy); letter-spacing: -1px; margin-bottom: 6px; }
  .day ul { list-style: none; }
  .day li { font-size: 10.6px; font-weight: 700; line-height: 17.2px; white-space: nowrap; text-transform: uppercase; }
  .day li b { color: var(--navy); font-weight: 700; }
</style>
</head>
<body>
<div class="flyer">
  <svg class="backdrop" width="851" height="1200" viewBox="0 0 851 1200" aria-hidden="true">
    <rect x="0" y="0" width="851" height="1200" fill="#1fa4ea"/>
    <polygon points="0,0 290,0 290,340 0,340" fill="#1b9fe2"/>
    <polygon points="0,0 290,0 290,123 150,104 140,110 130,104 0,104" fill="#22a6ec"/>
    <polygon points="0,240 290,250 290,340 0,340" fill="#1594d6"/>
    <polygon points="0,600 851,600 851,700 160,700 150,708 140,700 0,700" fill="#22a6ec"/>
    <polygon points="0,700 851,700 851,1200 0,1200" fill="#0f8ccf"/>
    <polygon points="0,1175 851,1160 851,1200 0,1200" fill="#22a6ec"/>
  </svg>

  <div class="photo photo-group" role="img" aria-label="Photo of a group class training with kettlebells in the gym"></div>
  <div class="photo photo-boxing" role="img" aria-label="Photo of a woman in boxing gloves striking a pad in the ring"></div>
  <div class="photo photo-kettlebell" role="img" aria-label="Photo of a man swinging a kettlebell in the gym"></div>

  <h1 class="brand-name">RIVERSTONE<br>PULSE<br>GYM</h1>
  <div class="brand-dot"></div>

  <div class="intro">
    <p>Riverstone Pulse Gym is a fun community of humble people.</p>
    <p>Our goal is to help guide you towards a fitter, healthier lifestyle!</p>
  </div>

  <div class="contact loc">OUR LOCATION:<br>Unit 27C<br>214 Kelvane Road<br>Marrow Heath<br>Glasgow<br>G72QT</div>
  <div class="contact tel">PHONE:<br>0793 062 51 84<span class="web">www.riverstonepulsegym-example.com</span></div>

  <h2 class="programs-title">OUR PROGRAMS</h2>

  <div class="timeline" style="left:356px;top:410px;height:140px"></div>
  <div class="node" style="left:345px;top:403px"></div>
  <div class="node" style="left:345px;top:462px"></div>
  <div class="node" style="left:345px;top:521px"></div>

  <div class="timeline" style="left:580px;top:325px;height:225px"></div>
  <div class="node" style="left:569px;top:323px"></div>
  <div class="node" style="left:569px;top:402px"></div>
  <div class="node" style="left:569px;top:461px"></div>
  <div class="node" style="left:569px;top:531px"></div>

  <div class="program" style="left:384px;top:408px">
    <h3>HIIT</h3>
    <p>High intensity interval training is 30-45 minutes of fat burning fun. The class is a mix of cardio, bodyweight and some resistance movements.</p>
  </div>
  <div class="program" style="left:384px;top:468px">
    <h3>CONDITIONING</h3>
    <p>A full hour of strength, cardio and bodyweight training to get you in tip top shape. Expect a mix of barbells, kettlebells, rowing machines, bikes and other training methods.</p>
  </div>
  <div class="program" style="left:384px;top:527px">
    <h3>BWS</h3>
    <p>This is our big Friday session to set you up for the weekend. 90 minutes of hard training that is done with a team emphasis. From heavy lifting to cardio triathlons, this class has it all but not for the faint hearted.</p>
  </div>

  <div class="program" style="left:605px;top:328px;width:215px">
    <h3>MUAY THAI</h3>
    <p>Commonly known as the science of 8 limbs you will learn how to punch, kick, knee and elbow. Thailands national sport is a great way to get your fitness kick. We train the complete beginner all the way to international fighters so you are in great hands.</p>
  </div>
  <div class="program" style="left:605px;top:408px;width:215px">
    <h3>KIDS MUAY THAI</h3>
    <p>Our junior program starts from age 6 onwards. Muay Thai is a great way for kids to get active and fit while learning new skills. Training in martial arts also teaches self discipline and socialisation skills.</p>
  </div>
  <div class="program" style="left:605px;top:469px;width:215px">
    <h3>YOGA</h3>
    <p>A combination of physical and mental practises that will leave you focused and refreshed for whatever the week throws at you. We always recommend our yoga classes as a great way to balance the high intensity training we offer.</p>
  </div>
  <div class="program" style="left:605px;top:537px;width:215px">
    <h3>Q-PRESS</h3>
    <p>Strength training with a little bit of conditioning. We regularly update the program and re test lifts to ensure you are making progress and getting stronger.</p>
  </div>

  <h2 class="timetable-title">TIMETABLE</h2>
  <div class="timetable-brand"><div class="dot"></div><span>RIVERSTONE<br>PULSE GYM</span></div>

  <div class="day" style="right:593px;top:734px">
    <h4>MON</h4>
    <ul>
      <li><b>7AM</b> Conditioning</li>
      <li><b>8AM</b> Open Gym</li>
      <li><b>10AM</b> Q-Press</li>
      <li><b>12:10PM</b> Lunch Time HIIT</li>
      <li><b>4PM</b> Open Gym</li>
      <li><b>5PM</b> Q-Press</li>
      <li><b>6PM</b> Fundamentals</li>
      <li><b>6PM</b> Muay Thai Foundations</li>
      <li><b>7PM</b> Strength and Conditioning</li>
    </ul>
  </div>
  <div class="day" style="right:408px;top:734px">
    <h4>TUE</h4>
    <ul>
      <li><b>6AM</b> Q-Press</li>
      <li><b>7AM</b> Fight Camp Muay Thai</li>
      <li><b>8AM</b> Open Gym</li>
      <li><b>12:10PM</b> Lunch Time HIIT</li>
      <li><b>4PM</b> Open Gym</li>
      <li><b>5:15PM</b> HIIT (0/30)</li>
      <li><b>6PM</b> Conditioning</li>
      <li><b>6PM</b> Kids</li>
      <li><b>7PM</b> Muay Thai Intermediate</li>
    </ul>
  </div>
  <div class="day" style="right:591px;top:948px">
    <h4>WED</h4>
    <ul>
      <li><b>6AM</b> Strength and Conditioning</li>
      <li><b>7AM</b> Yoga (0/25)</li>
      <li><b>8AM</b> Open Gym</li>
      <li><b>10AM</b> Q-Press</li>
      <li><b>4PM</b> Open Gym</li>
      <li><b>5PM</b> Q-Press</li>
      <li><b>5:15PM</b> HIIT (0/30)</li>
      <li><b>6PM</b> Fundamentals</li>
      <li><b>6PM</b> Muay Thai Foundations</li>
      <li><b>7:15PM</b> Yoga (0/25)</li>
    </ul>
  </div>
  <div class="day" style="right:407px;top:948px">
    <h4>THU</h4>
    <ul>
      <li><b>7AM</b> Conditioning</li>
      <li><b>8AM</b> Open Gym</li>
      <li><b>12:10PM</b> Lunch Time HIIT</li>
      <li><b>4PM</b> Open Gym</li>
      <li><b>5:15PM</b> HIIT (0/30)</li>
      <li><b>6PM</b> Conditioning</li>
      <li><b>6PM</b> Kids</li>
      <li><b>7PM</b> Muay Thai Intermediate</li>
    </ul>
  </div>
  <div class="day" style="right:231px;top:948px">
    <h4>FRI</h4>
    <ul>
      <li><b>6AM</b> Q-Press</li>
      <li><b>7AM</b> Fight Camp Muay Thay</li>
      <li><b>8AM</b> Open Gym</li>
      <li><b>10AM</b> Q-Press</li>
      <li><b>12:10PM</b> Lunch Time HIIT</li>
      <li><b>4PM</b> Open Gym</li>
      <li><b>5PM</b> Q-Press</li>
      <li><b>6PM</b> BWS</li>
    </ul>
  </div>
  <div class="day" style="right:43px;top:948px">
    <h4>SAT</h4>
    <ul>
      <li><b>10AM</b> Saturday Circuit</li>
      <li><b>11AM</b> Open Gym</li>
      <li><b>11AM</b> Fundamentals</li>
      <li><b>11AM</b> Kids</li>
      <li><b>12PM</b> Muay Thai Foundations</li>
    </ul>
  </div>
</div>
</body>
</html>
```